Mayhon online ordering platform looking for a great web design

Mayhon - from the Vietnamese words Mây Hồng meaning financial success.
Background
Mayhon is an online ordering platform for small retail businesses (corner stores). The idea is that small retailers will use the website to order their supplies. From this we will utilise the group buying to get better deals for them that they could not achieve individually.
We are looking for a simple but stylish design for our ordering page. The layout needs to be efficient, logical and self explanatory.
Products to be sold on the site are FMCG (fast moving consumer goods). Potential to be 000's of items.
Considerations
- end users are not technologically adept.
- Users are generally older so small print will not be well received.
- Use of touch screen monitors to select/change items so spacing in design is vital.
- Logical display of category and sub-categories.
- Easy selection of products to order as well as modification of quantity.
- Shopping cart with easy change of item quantity.
- List of items for ordering can be paginated.
- Items listed will have image for easy identification.
- Search box
- Format should be in psd (photoshop) or complete html/css
- All this information needs to be displayed on the one page.
Product information to contain the following:
- Image
- Price
- Product name
- Size
Area for prominent display of specials without crowding the product information.

```html
<!DOCTYPE html>
<html lang="en">
<head>
<meta charset="utf-8">
<title>Sub Category – Ordering</title>
<link href="https://fonts.googleapis.com/css2?family=Ubuntu:ital,wght@0,400;0,500;0,700;1,400&display=swap" rel="stylesheet">
<style>
:root{
  --bg:#ffffff;
  --border:#e3e3e3;
  --text:#2b2b2b;
  --muted:#8a8a8a;
  --green:#8cb04e;
  --red:#d8262b;
  --yellow:#d9c64a;
  --highlight:#f1f1f1;
}
*{box-sizing:border-box;margin:0;padding:0}
html,body{width:1200px;height:1195px;overflow:hidden;background:var(--bg);font-family:"Ubuntu",sans-serif;color:var(--text)}
.page{position:relative;width:1200px;height:1195px}
.breadcrumb{position:absolute;left:223px;top:7px;font-size:8.5px;color:var(--muted)}
.breadcrumb .current{color:var(--text)}
.grid{position:absolute;left:223px;top:32px;display:grid;grid-template-columns:repeat(4,137px);grid-auto-rows:210px;column-gap:17px;row-gap:19px}
.card{position:relative;border:1px solid var(--border);background:#fff;overflow:hidden}
.card.is-active{background:var(--highlight)}
.card.is-active .thumb{background-color:#fff;box-shadow:0 0 0 7px #fff}
.thumb{position:absolute;left:50%;top:16px;transform:translateX(-50%);width:40px;height:118px;border-radius:12px 12px 6px 6px}
.thumb.wide{width:108px;height:58px;top:60px;border-radius:8px}
.thumb.round{width:52px;height:110px;border-radius:22px}
.name{position:absolute;left:8px;top:147px;width:96px;font-size:10.4px;line-height:14.4px}
.size{position:absolute;left:8px;top:177px;font-size:8.8px;color:var(--muted)}
.price{position:absolute;left:8px;top:190px;font-size:12px;font-weight:700}
.price s{font-weight:500;color:#555;margin-right:2px}
.add{position:absolute;right:7px;top:184px;width:33px;height:17px;background:var(--green);color:#fff;font-size:9.6px;line-height:17px;text-align:center;border-radius:1px}
.in-cart{position:absolute;right:10px;top:166px;display:flex;align-items:center;gap:3px}
.badge{width:12px;height:12px;border-radius:50%;background:var(--red);color:#fff;font-size:7.5px;font-weight:700;line-height:12px;text-align:center}
.tag-featured{position:absolute;right:-2px;top:4px;background:var(--yellow);color:#fff;font-size:9px;padding:3px 7px}
.tag-tab{position:absolute;right:0;top:0;background:var(--green);color:#fff;font-size:9.6px;padding:4px 8px 5px 22px;border-bottom-left-radius:22px}
.ribbon{position:absolute;right:-28px;top:14px;width:120px;transform:rotate(38deg);text-align:center;color:#fff;font-size:10px;font-weight:700;font-style:italic;padding:3px 0}
.ribbon.red{background:var(--red)}
.ribbon.green{background:var(--green);font-weight:500}
.sidebar{position:absolute;left:838px;top:32px;width:137px}
.cart-box{position:relative;height:56px;border:1px solid var(--border);margin-bottom:8px}
.cart-title{position:absolute;left:8px;top:10px;font-size:11px;font-weight:700}
.cart-count{position:absolute;left:8px;top:26px;font-size:8px;font-style:italic}
.cart-total{position:absolute;right:10px;top:10px;font-size:11px;font-weight:700}
.checkout{position:absolute;right:8px;top:30px;width:55px;height:19px;background:var(--green);color:#fff;font-size:8.8px;line-height:19px;text-align:center}
.cart-item{position:relative;height:142px;border:1px solid var(--border);margin-bottom:8px}
.cart-item .thumb{left:24px;transform:none;width:20px;height:48px;border-radius:6px}
.cart-item .name{top:76px}
.cart-item .in-cart{top:94px;right:12px}
.cart-item .price{top:122px}
.qty{position:absolute;top:116px;width:19px;height:18px;color:#fff;font-size:10px;line-height:18px;text-align:center}
.qty.minus{left:86px;background:var(--red)}
.qty.plus{left:109px;background:var(--green)}
.c-white{background:linear-gradient(#39a2dc 0 30%,#eef3f6 30%)}
.c-orange{background:linear-gradient(#2b58c8 0 12%,#d58a3a 12%)}
.c-green{background:linear-gradient(#1e8a3a,#36a844)}
.c-amber{background:linear-gradient(#e86a1e 0 15%,#f6a327 15%)}
.c-purple{background:linear-gradient(#6a2fa0,#3a1d78)}
.c-honey{background:linear-gradient(#3a2a1c 0 15%,#efe2b8 15%)}
.c-yellow{background:linear-gradient(#f2b400 0 15%,#fbd70f 15%)}
.c-sky{background:linear-gradient(#2a76c8 0 20%,#f1f5fb 20%)}
.c-black{background:linear-gradient(#161616,#2a2a2a)}
.c-pink{background:linear-gradient(#f2b6d0,#e07ba8)}
.c-wave{background:linear-gradient(#2e7fd6 0 35%,#f3a633 35%)}
.c-multi{background:linear-gradient(90deg,#d93b3b,#3bb34a 30%,#8fd13b 60%,#3bb34a)}
.c-lemon{background:linear-gradient(#f0e64a,#fff21a)}
.c-blush{background:linear-gradient(#c8b3dd 0 20%,#f6d3e2 20%)}
.c-pearl{background:linear-gradient(#1e2f6e 0 18%,#f4f4f2 18%)}
</style>
</head>
<body>
<svg width="0" height="0" style="position:absolute">
  <symbol id="cart" viewBox="0 0 14 12"><path d="M1 1h2l2 7h7l1.5-5H4" fill="none" stroke="#d8262b" stroke-width="1.6" stroke-linejoin="round"/><circle cx="6" cy="10.5" r="1.1" fill="#d8262b"/><circle cx="11" cy="10.5" r="1.1" fill="#d8262b"/></symbol>
</svg>
<div class="page">
  <div class="breadcrumb">Home &gt; Main Category &gt; <span class="current">Sub Category</span></div>

  <div class="grid">
    <div class="card"><div class="thumb c-white" role="img" aria-label="Shampoo bottle photo"></div><div class="name">Product Name Lorem Impsum</div><div class="size">500 ml</div><div class="price"><s>$2.99</s> $2.99</div><div class="add">Add</div></div>
    <div class="card"><div class="thumb c-orange" role="img" aria-label="Shampoo bottle photo"></div><div class="name">Product Name Lorem Impsum</div><div class="in-cart"><svg width="13" height="11"><use href="#cart"/></svg><span class="badge">1</span></div><div class="size">500 ml</div><div class="price">$2.99</div><div class="add">Add</div></div>
    <div class="card"><div class="thumb c-green" role="img" aria-label="Shampoo bottle photo"></div><div class="name">Product Name Lorem Impsum</div><div class="size">500 ml</div><div class="price">$2.99</div><div class="add">Add</div></div>
    <div class="card"><div class="thumb c-amber" role="img" aria-label="Shampoo bottle photo"></div><div class="name">Product Name Lorem Impsum</div><div class="in-cart"><svg width="13" height="11"><use href="#cart"/></svg><span class="badge">5</span></div><div class="size">500 ml</div><div class="price"><s>$2.99</s> $2.99</div><div class="add">Add</div></div>

    <div class="card"><div class="thumb c-purple" role="img" aria-label="Shampoo bottle photo"></div><div class="ribbon red">20% Off</div><div class="name">Product Name Lorem Impsum</div><div class="in-cart"><svg width="13" height="11"><use href="#cart"/></svg><span class="badge">5</span></div><div class="size">500 ml</div><div class="price">$2.99</div><div class="add">Add</div></div>
    <div class="card"><div class="thumb c-honey" role="img" aria-label="Pump shampoo bottle photo"></div><div class="name">Product Name Lorem Impsum</div><div class="size">500 ml</div><div class="price">$2.99</div><div class="add">Add</div></div>
    <div class="card"><div class="thumb c-yellow" role="img" aria-label="Baby shampoo bottle photo"></div><div class="tag-featured">Featured</div><div class="name">Product Name Lorem Impsum</div><div class="in-cart"><svg width="13" height="11"><use href="#cart"/></svg><span class="badge">2</span></div><div class="size">500 ml</div><div class="price">$5.99</div><div class="add">Add</div></div>
    <div class="card"><div class="thumb c-sky" role="img" aria-label="Shampoo bottle photo"></div><div class="name">Product Name Lorem Impsum</div><div class="size">500 ml</div><div class="price">$2.99</div><div class="add">Add</div></div>

    <div class="card"><div class="thumb c-black" role="img" aria-label="Shampoo bottle photo"></div><div class="name">Product Name Lorem Impsum</div><div class="size">500 ml</div><div class="price"><s>$2.99</s> $2.99</div><div class="add">Add</div></div>
    <div class="card"><div class="thumb c-pink" role="img" aria-label="Shampoo bottle photo"></div><div class="name">Product Name Lorem Impsum</div><div class="in-cart"><svg width="13" height="11"><use href="#cart"/></svg><span class="badge">1</span></div><div class="size">500 ml</div><div class="price">$2.99</div><div class="add">Add</div></div>
    <div class="card is-active"><div class="thumb round c-wave" role="img" aria-label="Shampoo bottle photo"></div><div class="name">Product Name Lorem Impsum</div><div class="size">500 ml</div><div class="price">$2.99</div><div class="add">Add</div></div>
    <div class="card"><div class="thumb wide c-multi" role="img" aria-label="Row of shampoo bottles photo"></div><div class="name">Product Name Lorem Impsum</div><div class="in-cart"><svg width="13" height="11"><use href="#cart"/></svg><span class="badge">5</span></div><div class="size">500 ml</div><div class="price"><s>$2.99</s> $2.99</div><div class="add">Add</div></div>

    <div class="card"><div class="thumb c-lemon" role="img" aria-label="Baby shampoo bottle photo"></div><div class="name">Product Name Lorem Impsum</div><div class="in-cart"><svg width="13" height="11"><use href="#cart"/></svg><span class="badge">5</span></div><div class="size">500 ml</div><div class="price">$2.99</div><div class="add">Add</div></div>
    <div class="card"><div class="thumb c-white" role="img" aria-label="Shampoo bottle photo"></div><div class="ribbon green">Featured</div><div class="name">Product Name Lorem Impsum</div><div class="size">500 ml</div><div class="price">$2.99</div><div class="add">Add</div></div>
    <div class="card"><div class="thumb round c-blush" role="img" aria-label="Baby shampoo bottle photo"></div><div class="name">Product Name Lorem Impsum</div><div class="in-cart"><svg width="13" height="11"><use href="#cart"/></svg><span class="badge">2</span></div><div class="size">500 ml</div><div class="price">$5.99</div><div class="add">Add</div></div>
    <div class="card"><div class="thumb c-pearl" role="img" aria-label="Shampoo bottle photo"></div><div class="name">Product Name Lorem Impsum</div><div class="size">500 ml</div><div class="price">$2.99</div><div class="add">Add</div></div>

    <div class="card"><div class="thumb c-white" role="img" aria-label="Shampoo bottle photo"></div><div class="name">Product Name Lorem Impsum</div><div class="size">500 ml</div><div class="price"><s>$2.99</s> $2.99</div><div class="add">Add</div></div>
    <div class="card"><div class="thumb c-pink" role="img" aria-label="Shampoo bottle photo"></div><div class="name">Product Name Lorem Impsum</div><div class="in-cart"><svg width="13" height="11"><use href="#cart"/></svg><span class="badge">1</span></div><div class="size">500 ml</div><div class="price">$2.99</div><div class="add">Add</div></div>
    <div class="card"><div class="thumb c-black" role="img" aria-label="Shampoo bottle photo"></div><div class="tag-tab">Featured</div><div class="name">Product Name Lorem Impsum</div><div class="size">500 ml</div><div class="price">$2.99</div><div class="add">Add</div></div>
    <div class="card"><div class="thumb c-purple" role="img" aria-label="Shampoo bottle photo"></div><div class="name">Product Name Lorem Impsum</div><div class="in-cart"><svg width="13" height="11"><use href="#cart"/></svg><span class="badge">5</span></div><div class="size">500 ml</div><div class="price"><s>$2.99</s> $2.99</div><div class="add">Add</div></div>

    <div class="card"></div><div class="card"></div><div class="card"></div><div class="card"></div>
  </div>

  <aside class="sidebar">
    <div class="cart-box"><div class="cart-title">My Cart</div><div class="cart-count">12 Items</div><div class="cart-total">$45.99</div><div class="checkout">Checkout</div></div>
    <div class="cart-item"><div class="thumb c-white" role="img" aria-label="Shampoo bottle photo"></div><div class="name">Product Name Lorem Impsum</div><div class="in-cart"><svg width="13" height="11"><use href="#cart"/></svg><span class="badge">5</span></div><div class="price"><s>$2.99</s> $2.99</div><div class="qty minus">–</div><div class="qty plus">+</div></div>
    <div class="cart-item"><div class="thumb c-white" role="img" aria-label="Shampoo bottle photo"></div><div class="name">Product Name Lorem Impsum</div><div class="in-cart"><svg width="13" height="11"><use href="#cart"/></svg><span class="badge">5</span></div><div class="price"><s>$2.99</s> $2.99</div><div class="qty minus">–</div><div class="qty plus">+</div></div>
    <div class="cart-item"><div class="thumb c-white" role="img" aria-label="Shampoo bottle photo"></div><div class="name">Product Name Lorem Impsum</div><div class="in-cart"><svg width="13" height="11"><use href="#cart"/></svg><span class="badge">5</span></div><div class="price"><s>$2.99</s> $2.99</div><div class="qty minus">–</div><div class="qty plus">+</div></div>
  </aside>
</div>
</body>
</html>
```